Small Business Consulting Firm Needs Letterhead

We need a letterhead for our company "Brightpath Plus". Our company does outbound calling and mailing to business owner's companies who have taken high interest loans. These loans tend to put these businesses in a big financial bind short term, and we help them find better financial options. We would like the design to match our colors of our logo. Headers and footers would look nice, but we are open. We would want it to include our address, website, phone, and email info. Our address - 2000 E. Lamar Blvd. Suite 600Website - www.safeguardtoday.comEmail - info@safeguardtoday.comPhone - 855-726-1938
Industry/Entity Type
Financial Planning
Look and feel
Each slider illustrates characteristics of the customer's brand and the style your logo design should communicate.

```html
<!DOCTYPE html>
<html lang="en">
<head>
<meta charset="utf-8">
<title>Brightpath Plus Letterhead</title>
<link rel="stylesheet" href="https://fonts.googleapis.com/css2?family=Tinos&family=Arimo&family=Montserrat:wght@400&family=Courier+Prime&display=swap">
<style>
  :root {
    --blue-deep: #1055c8;
    --blue-light: #2e98fa;
    --green: #52cf00;
    --lime: #6ef700;
    --ink: #1a1a1a;
    --brand-ink: #2f3b3f;
    --paper: #ffffff;
    --signature-tone: #d9d9d9;
  }
  * { margin: 0; padding: 0; box-sizing: border-box; }
  html, body { width: 856px; height: 1200px; overflow: hidden; background: var(--paper); }
  .letterhead { position: relative; width: 856px; height: 1200px; background: var(--paper); }

  .band { position: absolute; height: 20px; width: 255px; }
  .band--top { top: 13px; }
  .band--bottom { top: 1158px; }
  .band--left { left: 13px; }
  .band--center { left: 301px; }
  .band--right { left: 588px; }
  .band--top.band--left, .band--top.band--right { background: var(--blue-deep); }
  .band--top.band--center { background: var(--green); }
  .band--bottom.band--left, .band--bottom.band--right { background: var(--blue-light); }
  .band--bottom.band--center { background: var(--lime); }

  .brand { position: absolute; top: 88px; left: 0; width: 856px; text-align: center; }
  .brand__mark { display: block; width: 64px; height: 64px; margin: 0 auto 32px; background: var(--green); }
  .brand__name {
    font-family: "Montserrat", sans-serif; font-weight: 400;
    font-size: 29px; letter-spacing: 3px; color: var(--brand-ink);
    text-transform: uppercase;
  }

  .letter {
    position: absolute; top: 320px; left: 116px; width: 636px;
    font-family: "Tinos", serif; font-size: 13px; line-height: 16.8px; color: var(--ink);
  }
  .letter__date { margin-bottom: 17px; }
  .letter__recipient { margin-bottom: 48px; }
  .letter__salutation { margin-bottom: 17px; }
  .letter__body p { margin-bottom: 17px; }
  .letter__closing { margin-top: 42px; }

  .signature { position: absolute; top: 836px; left: 116px; width: 70px; height: 32px; background: var(--signature-tone); border-radius: 3px; }
  .signer { position: absolute; top: 878px; left: 113px; font-family: "Arimo", sans-serif; font-size: 18px; color: var(--ink); }

  .contact {
    position: absolute; top: 1010px; left: 0; width: 856px; text-align: center;
    font-family: "Courier Prime", monospace; font-size: 21px; line-height: 30px; color: var(--ink);
  }
  .contact__line { display: block; }
</style>
</head>
<body>
<div class="letterhead">
  <div class="band band--top band--left"></div>
  <div class="band band--top band--center"></div>
  <div class="band band--top band--right"></div>

  <header class="brand">
    <span class="brand__mark"></span>
    <div class="brand__name">Brightpath Plus</div>
  </header>

  <main class="letter">
    <p class="letter__date">August 28, 2011</p>
    <p class="letter__recipient">First Last Name<br>Street Address<br>City, State 00000</p>
    <p class="letter__salutation">Dear :</p>
    <div class="letter__body">
      <p>Lorem ipsum dolor sit amet, consectetur adipiscing elit. Aenean ut ipsum eget massa hendrerit vestibulum vel in velit. Donec pretium neque velit.</p>
      <p>Aliquam porta lectus nec mauris ornare venenatis. Vivamus non est turpis, et cursus sem. Mauris vehicula erat in diam auctor at bibendum nisl lacinia. Morbi imperdiet neque vehicula nunc convallis gravida. Vestibulum iaculis pretium placerat. Integer consequat, est sit amet facilisis eleifend, nibh nibh varius orci, eget dapibus arcu dui non purus.</p>
      <p>Pellentesque in magna mauris. Duis enim sapien, dictum vitae condimentum a, pulvinar vel lacus. Mauris et molestie nibh. Vestibulum vitae nulla at metus elementum porta sit amet interdum elit. Nulla sollicitudin neque eu nulla volutpat congue.</p>
      <p>Etiam pellentesque, velit id dapibus fermentum, turpis sapien ornare dui, ac tincidunt ligula odio congue purus. Nunc sed ante dui, in porta lectus. Cras nec sem lorem. In hac habitasse platea dictumst. Maecenas id diam quis dui porta tristique. Sed id egestas felis. Donec ullamcorper mattis posuere. Phasellus fermentum eleifend tortor vel dapibus. Vestibulum ante ipsum.</p>
    </div>
    <p class="letter__closing">Sincerely,</p>
  </main>

  <div class="signature" role="img" aria-label="Handwritten signature of the sender"></div>
  <p class="signer">Tran Minh Khoa</p>

  <footer class="contact">
    <span class="contact__line">4170 W. Corwin Ave. Suite 310</span>
    <span class="contact__line">855-726-1938</span>
    <span class="contact__line">www.brightpathplus.com</span>
    <span class="contact__line">info@brightpathplus.com</span>
  </footer>

  <div class="band band--bottom band--left"></div>
  <div class="band band--bottom band--center"></div>
  <div class="band band--bottom band--right"></div>
</div>
</body>
</html>
```